Web Design Project

Please take a look at my current aged website www.talvikhrconsulting.com and my newly designed logo and business cards. I would like a new fresh updated look to my website and my new designs incorporated.
Updates

  Good Morning Everyone

Due to an Austrralian licencing issue I have had to have my logo slightly redesigned.

Would you please be able to look at the newly uploaded files and revise your designs.

Thanks so much.  I am very happy with the calibre and quality of the designs so far.

kind Regards

Marla

Industry/Entity Type

Business

Requirements
Must have
• the exisiting pages and fresh new graphics and a real commitment to my palette of lime green, turqouise and black.

```html
<!DOCTYPE html>
<html lang="en">
<head>
<meta charset="utf-8">
<title>Talvik HR Consulting – Our Services</title>
<link href="https://fonts.googleapis.com/css2?family=Arimo&family=Archivo+Narrow&family=Source+Sans+3:wght@400&display=swap" rel="stylesheet">
<style>
  :root {
    --backdrop: #9a9a9a;
    --page: #ffffff;
    --ink: #111111;
    --muted: #6b6b6b;
    --nav-ink: #555555;
    --lime: #72b83a;
    --lime-pale: #dbe8cf;
    --band: #dde5d8;
    --turquoise: #3aa8c8;
    --ring: #c9c9c9;
    --ring-inner: #e3e3e3;
    --footer-ink: #ffffff;
  }
  * { margin: 0; padding: 0; box-sizing: border-box; }
  html, body { width: 1082px; height: 1200px; overflow: hidden; background: var(--backdrop); }
  .stage {
    position: absolute; left: 0; top: 0; width: 1012px; height: 1122px;
    transform: scale(1.0692, 1.0695); transform-origin: 0 0;
    font-family: "Source Sans 3", "Myriad Pro", sans-serif;
  }
  .page {
    position: absolute; left: 175px; top: 10px; width: 661px; height: 1066px;
    background: var(--page); box-shadow: 0 0 14px rgba(0,0,0,.55), 6px 6px 10px rgba(0,0,0,.35);
    overflow: hidden;
  }
  .side-stripe {
    position: absolute; left: 0; top: 0; width: 22px; height: 100%;
    background: linear-gradient(to bottom, #eef3ea 0%, var(--lime-pale) 25%, #a8d07f 60%, var(--lime) 100%);
  }
  .header-swoosh { position: absolute; left: 22px; top: 0; }
  .brand-mark {
    position: absolute; left: 47px; top: 38px; width: 88px; height: 88px;
    border-radius: 50%; border: 5px solid var(--turquoise);
  }
  .brand-name {
    position: absolute; left: 166px; top: 18px; font-family: "Arimo", Arial, sans-serif;
    font-size: 31px; color: var(--ink); letter-spacing: -.2px;
  }
  .brand-tagline {
    position: absolute; left: 224px; top: 56px; font-family: "Arimo", Arial, sans-serif;
    font-size: 12.5px; color: var(--muted);
  }
  .section-band {
    position: absolute; left: 22px; height: 30px; padding-left: 57px;
    font-size: 19px; line-height: 30px; color: var(--ink);
  }
  .band-people { top: 264px; width: 460px; background: linear-gradient(to right, var(--band) 60%, rgba(221,229,216,0)); }
  .band-relations { top: 539px; width: 638px; background: linear-gradient(to right, var(--band) 45%, #fff 70%, var(--band) 100%); }
  .band-organisation { top: 774px; width: 634px; background: linear-gradient(to right, var(--band) 45%, #fff 70%, var(--band) 100%); }
  .service-list { position: absolute; left: 80px; list-style: none; font-size: 15.5px; line-height: 20px; color: var(--ink); }
  .list-people { top: 305px; }
  .list-relations { top: 583px; left: 79px; }
  .list-organisation { top: 820px; left: 79px; }
  .page-foot {
    position: absolute; left: 22px; top: 1009px; width: 639px; height: 57px;
    background: linear-gradient(to right, var(--band) 40%, #fff 75%, var(--band) 100%);
  }
  .nav-dial { position: absolute; left: 715px; top: 145px; }
  .nav-label { position: absolute; font-family: "Archivo Narrow", "Arial Narrow", sans-serif; font-size: 18px; color: var(--nav-ink); }
  .nav-home { left: 700px; top: 151px; }
  .nav-services { left: 618px; top: 181px; width: 104px; height: 28px; padding-left: 14px; line-height: 28px; color: var(--ink); background: linear-gradient(to right, var(--lime-pale), #e9f0e2); }
  .nav-consultants { left: 601px; top: 220px; }
  .nav-fees { left: 656px; top: 258px; }
  .nav-contact { left: 751px; top: 315px; }
  .footer-nav {
    position: absolute; left: 196px; top: 1085px; display: flex; list-style: none;
    font-size: 16px; color: var(--footer-ink);
  }
  .footer-nav li { padding: 0 10px; line-height: 26px; border-left: 1px solid var(--footer-ink); }
  .footer-nav li:first-child { border-left: none; }
  .copyright {
    position: absolute; left: 701px; top: 1088px; font-size: 15px; color: var(--footer-ink);
    text-shadow: 1px 1px 1px rgba(0,0,0,.6);
  }
</style>
</head>
<body>
<div class="stage">
  <div class="page">
    <div class="side-stripe"></div>
    <svg class="header-swoosh" width="639" height="220" viewBox="0 0 639 220" aria-hidden="true">
      <defs>
        <linearGradient id="swooshFill" x1="0" y1="0" x2="1" y2="1">
          <stop offset="0" stop-color="#ececec"/>
          <stop offset="1" stop-color="#c8c8c8"/>
        </linearGradient>
      </defs>
      <path d="M0 0 H639 V88 Q260 110 0 208 Z" fill="url(#swooshFill)"/>
      <path d="M0 208 Q260 110 639 88" fill="none" stroke="#ffffff" stroke-width="3"/>
    </svg>
    <div class="brand-mark"></div>
    <div class="brand-name">Talvik HR Consulting</div>
    <div class="brand-tagline">Outsourced Human Resources Solutions and Stragedies</div>

    <div class="section-band band-people">People Systems and Processes</div>
    <ul class="service-list list-people">
      <li>Attraction, Recruitment and Induction</li>
      <li>Remuneration, Benefits and Salary</li>
      <li>Talent Management and Retention</li>
      <li>Graduate Management</li>
      <li>Performance Management and Planning</li>
      <li>Conflict, Dispute and Grievance Facilitation and Resolution Workforce Planning</li>
      <li>Reward and Recognition</li>
      <li>Leadership Programs</li>
      <li>Career Counselling</li>
      <li>Coaching and Mentoring</li>
    </ul>

    <div class="section-band band-relations">Employee Relations</div>
    <ul class="service-list list-relations">
      <li>HR Function Review and Assessments</li>
      <li>Industrial Relations advice</li>
      <li>Contracts of Employment</li>
      <li>Industrial Award Service</li>
      <li>Employee Entitlements</li>
      <li>Equal Opportunity</li>
      <li>Union issues</li>
      <li>Termination</li>
    </ul>

    <div class="section-band band-organisation">Organisation Development</div>
    <ul class="service-list list-organisation">
      <li>Policy &amp; Procedure Development and Auditing</li>
      <li>Organisation Evaluation and Re-design</li>
      <li>Culture and Values Asssessment and Planning</li>
    </ul>

    <div class="page-foot"></div>
  </div>

  <svg class="nav-dial" width="175" height="175" viewBox="0 0 175 175" aria-hidden="true">
    <circle cx="87" cy="85" r="83" fill="#b9b9b9"/>
    <circle cx="87" cy="85" r="80" fill="var(--ring)"/>
    <circle cx="87" cy="85" r="62" fill="var(--ring-inner)" stroke="#ffffff" stroke-width="2"/>
    <path d="M22 38 A80 80 0 0 1 45 17" fill="none" stroke="var(--turquoise)" stroke-width="16"/>
    <path d="M13 58 A80 80 0 0 1 20 42" fill="none" stroke="var(--lime)" stroke-width="16"/>
    <path d="M10 78 A80 80 0 0 1 12 64" fill="none" stroke="var(--turquoise)" stroke-width="16"/>
    <path d="M13 110 A80 80 0 0 1 10 96" fill="none" stroke="var(--turquoise)" stroke-width="16"/>
    <path d="M127 152 A80 80 0 0 1 47 152" fill="none" stroke="var(--turquoise)" stroke-width="14"/>
    <circle cx="87" cy="85" r="26" fill="none" stroke="#ffffff" stroke-width="3"/>
  </svg>
  <div class="nav-label nav-home">Home</div>
  <div class="nav-label nav-services">Our Services</div>
  <div class="nav-label nav-consultants">Our Consultants</div>
  <div class="nav-label nav-fees">Our Fees</div>
  <div class="nav-label nav-contact">Contact Us</div>

  <ul class="footer-nav">
    <li>Home</li>
    <li>Our Services</li>
    <li>Our Consultants</li>
    <li>Our Fees</li>
    <li>Contact Us</li>
  </ul>
  <div class="copyright">Copyright 2012 ©</div>
</div>
</body>
</html>
```